Tall Fern Roofing Business Card

Need a business card with the logo that was designed here

Contact Information for Business Card

Name, Title, Phone, Email, Website, Company name

```html
<!DOCTYPE html>
<html lang="en">
<head>
<meta charset="UTF-8">
<title>Tall Fern Roofing Business Card</title>
<link href="https://fonts.googleapis.com/css2?family=Montserrat:wght@400;500;700&display=swap" rel="stylesheet">
<style>
  :root {
    --page-bg: #ebebed;
    --card-front: #7f7e7f;
    --card-back: #ffffff;
    --brand-blue: #3b6fbf;
    --ink-grey: #6b6b6b;
    --silver: #c9c9cb;
    --line-blue: #6f93cf;
  }
  * { margin: 0; padding: 0; box-sizing: border-box; }
  html, body {
    width: 1200px;
    height: 900px;
    overflow: hidden;
    background: var(--page-bg);
    font-family: "Montserrat", sans-serif;
  }
  .canvas {
    width: 1200px;
    height: 900px;
    display: flex;
    flex-direction: column;
    align-items: center;
    justify-content: center;
    gap: 40px;
  }
  .card {
    position: relative;
    width: 620px;
    height: 354px;
    box-shadow: 0 6px 18px rgba(0,0,0,0.12);
  }
  .card--front {
    background: var(--card-front);
    display: flex;
    align-items: center;
    justify-content: center;
  }
  .front-wordmark {
    display: flex;
    align-items: center;
    gap: 14px;
    color: var(--silver);
    font-weight: 700;
    font-size: 34px;
    letter-spacing: 1px;
  }
  .wordmark-square {
    width: 22px;
    height: 22px;
    background: var(--silver);
  }
  .card--back { background: var(--card-back); }
  .back-wordmark {
    position: absolute;
    left: 52px;
    top: 62px;
    display: flex;
    align-items: center;
    gap: 10px;
    color: var(--brand-blue);
    font-weight: 700;
    font-size: 24px;
    letter-spacing: 0.5px;
  }
  .back-wordmark .wordmark-square {
    width: 16px;
    height: 16px;
    background: var(--brand-blue);
  }
  .edge-tab {
    position: absolute;
    right: 0;
    top: 36px;
    width: 20px;
    height: 56px;
    background: var(--brand-blue);
  }
  .divider {
    position: absolute;
    left: 56px;
    top: 178px;
    width: 290px;
    height: 1.5px;
    background: var(--line-blue);
  }
  .person {
    position: absolute;
    right: 42px;
    top: 128px;
    text-align: left;
  }
  .person-name {
    color: var(--brand-blue);
    font-weight: 700;
    font-size: 25px;
    letter-spacing: 0.5px;
  }
  .person-title-row {
    display: flex;
    align-items: center;
    gap: 8px;
    margin-top: 4px;
    margin-left: 70px;
  }
  .person-title-row::before {
    content: "";
    width: 36px;
    height: 1.5px;
    background: var(--ink-grey);
  }
  .person-title {
    color: var(--ink-grey);
    font-size: 15px;
    font-weight: 400;
  }
  .contact {
    position: absolute;
    left: 56px;
    top: 200px;
    color: var(--ink-grey);
    font-size: 15px;
    line-height: 22px;
  }
  .contact-list { list-style: none; margin-top: 4px; }
  .contact-list li {
    display: flex;
    align-items: center;
    gap: 10px;
  }
  .contact-icon { width: 14px; height: 14px; flex: none; }
</style>
</head>
<body>
<main class="canvas">
  <section class="card card--front" aria-label="Card front">
    <div class="front-wordmark">
      <span class="wordmark-square"></span>
      <span>Tall Fern Roofing</span>
    </div>
  </section>

  <section class="card card--back" aria-label="Card back">
    <div class="back-wordmark">
      <span class="wordmark-square"></span>
      <span>Tall Fern Roofing</span>
    </div>
    <div class="edge-tab"></div>

    <div class="person">
      <div class="person-name">CALLUM HENSLEY</div>
      <div class="person-title-row"><span class="person-title">Managing Director</span></div>
    </div>

    <div class="divider"></div>

    <div class="contact">
      <p>415 W Harlow Street</p>
      <p>Marbury County 4187</p>
      <ul class="contact-list">
        <li>
          <svg class="contact-icon" viewBox="0 0 14 14" aria-hidden="true">
            <circle cx="7" cy="7" r="7" fill="#3b6fbf"/>
            <path d="M4.3 3.6c.4-.3.8-.2 1 .2l.6 1.1c.2.3.1.6-.2.8l-.4.3c.4.9 1 1.6 1.9 2.1l.3-.4c.2-.3.5-.4.8-.2l1.1.6c.4.2.5.6.2 1l-.5.6c-.4.4-1 .5-1.5.2C6 9.1 4.8 7.9 4 6.2c-.2-.5-.1-1.1.3-1.5z" fill="#fff"/>
          </svg>
          <span>0455 618 273</span>
        </li>
        <li>
          <svg class="contact-icon" viewBox="0 0 14 14" aria-hidden="true">
            <circle cx="7" cy="7" r="7" fill="#3b6fbf"/>
            <rect x="3.5" y="4.5" width="7" height="5" fill="none" stroke="#fff" stroke-width="1"/>
            <path d="M3.5 4.8 7 7.4l3.5-2.6" fill="none" stroke="#fff" stroke-width="1"/>
          </svg>
          <span>info@tallfernroofing.com</span>
        </li>
        <li>
          <svg class="contact-icon" viewBox="0 0 14 14" aria-hidden="true">
            <circle cx="7" cy="7" r="7" fill="#3b6fbf"/>
            <circle cx="7" cy="7" r="3.6" fill="none" stroke="#fff" stroke-width="0.9"/>
            <ellipse cx="7" cy="7" rx="1.5" ry="3.6" fill="none" stroke="#fff" stroke-width="0.9"/>
            <line x1="3.4" y1="7" x2="10.6" y2="7" stroke="#fff" stroke-width="0.9"/>
          </svg>
          <span>www.tallfernroofing.com</span>
        </li>
      </ul>
    </div>
  </section>
</main>
</body>
</html>
```